Exciting opportunity to create logo and a label for our natural health brand.

About us

We are a customer centric health supplement brand who believes in natural medicine and high quality ingredients. We take a holistic approach to healthcare, with an eastern philosophy. We believe in being partners with our customers in their health care journey and are invested in their well being.

Our brand philosophy and values are attached (see Vorna philosophy.png). Our personality traits are:

- Natural
- Fresh
- Modern
- Balanced (in a holistic sense)

Task breakdown

1. Design a fresh feeling logo for us
- We want it to represent our values and high quality ingredients. We would like the quality of the product to be reflected in the branding and have a high end feel.
- Logo text must include Vorna Health Sciences
- We want the Vorna to be the focus of the logo (see uploaded image Vorna logo example.png)
The logo does not have to follow this layout, but we just want the Vorna to stand out. Feel free to use your creative license on this!

2. Create an attractive label to go on the supplement bottle
- The designs need to be eye catching, give a sense of high end ingredients and natural products and tie in with the logo to give a joined up feel.
- We are selling our products online and need them to really stand out from the competition.
- See examples of labels and packaging we like (1 -7 label design).

The initial label we would like you to design would be for our product Calm Drift. It is a product that assists in the management of Anxiety and stress. The label will appear on the bottle that holds the capsules for this supplement, see uploaded files (Example plain bottles.png). The bottles may be white as the picture shows or dark blue recyclable plastic or dark brown glass . We don't have the exact dimensions of the bottle yet, but I will follow up with these.

The label needs to include the following things:
1. The logo
2. The name of the product
3. The product is to help with the relief of Anxiety and Stress
4. Number of capsules the bottle contains
5. The back of the label should have
i) The ingredients
ii) Dosage
iii) Directions of use

Please use placeholder text where needed.

We look forward to seeing your design. Thank you.

```html
<!DOCTYPE html>
<html lang="en">
<head>
<meta charset="UTF-8">
<title>Calm Drift – Vorna Health Sciences label</title>
<link rel="stylesheet" href="https://fonts.googleapis.com/css2?family=Bebas+Neue&family=Poppins:wght@300;400;500&family=Roboto+Condensed:wght@300;400;700&display=swap">
<style>
  :root {
    --page: #f3f3f0;
    --sage: #cfdcc8;
    --sage-deep: #c3d3bb;
    --sage-box: #b7c9ae;
    --forest: #1e4d2c;
    --rule: #3f6e4d;
    --ink: #2b2b2b;
    --ink-soft: #3a3a3a;
    --divider: #3a1d12;
    --white: #ffffff;
  }
  * { margin: 0; padding: 0; box-sizing: border-box; }
  html, body { width: 1200px; height: 1200px; overflow: hidden; background: var(--page); }
  .canvas { position: relative; width: 1200px; height: 1200px; }

  .label {
    position: absolute; top: 280px; height: 640px;
    background: linear-gradient(180deg, var(--sage) 0%, var(--sage-deep) 100%);
    overflow: hidden;
  }
  .band {
    position: absolute; left: 0; right: 0; bottom: 0; height: 52px;
    background: var(--forest); color: var(--white);
  }

  /* Front */
  .front { left: 30px; width: 560px; }
  .brand { position: absolute; left: 104px; top: 56px; }
  .brand-name {
    font-family: "Poppins", sans-serif; font-weight: 500; font-size: 82px;
    line-height: 1; color: var(--ink); letter-spacing: 1px;
  }
  .brand-rule { width: 226px; height: 2px; background: var(--rule); margin: 10px 0 6px 22px; }
  .brand-sub {
    font-family: "Poppins", sans-serif; font-weight: 400; font-size: 17px;
    letter-spacing: 2.4px; color: var(--ink-soft); margin-left: 22px;
  }
  .product-name {
    position: absolute; left: 92px; top: 318px;
    font-family: "Bebas Neue", sans-serif; font-size: 92px; line-height: 1;
    letter-spacing: 1px; color: var(--ink);
  }
  .claim-rule { position: absolute; left: 94px; width: 180px; height: 4px; background: var(--rule); }
  .claim-rule.top { top: 446px; }
  .claim-rule.bottom { top: 532px; width: 176px; }
  .claim {
    position: absolute; left: 94px; top: 462px;
    font-family: "Poppins", sans-serif; font-weight: 300; font-size: 20px;
    line-height: 28px; letter-spacing: 2.6px; color: var(--ink-soft);
  }
  .category {
    position: absolute; left: 94px; top: 552px;
    font-family: "Poppins", sans-serif; font-weight: 300; font-size: 20px;
    letter-spacing: 2.6px; color: var(--ink);
  }
  .front .band { padding: 12px 0 0 96px; font-family: "Poppins", sans-serif; font-size: 20px; letter-spacing: 2.6px; }
  .lotus-art {
    position: absolute; left: 330px; top: 410px; width: 230px; height: 200px;
    background: radial-gradient(ellipse at 50% 70%, rgba(255,255,255,0.55) 0%, rgba(150,190,150,0.35) 45%, rgba(207,220,200,0) 72%);
  }

  /* Back */
  .back-left { left: 610px; width: 272px; border-radius: 0 10px 0 0; }
  .back-right { left: 892px; width: 278px; border-radius: 10px 0 0 0; }
  .back-divider { position: absolute; left: 882px; top: 280px; width: 10px; height: 640px; background: var(--divider); }

  .facts-box {
    position: absolute; left: 0; top: 18px; width: 250px; height: 320px;
    background: var(--white); border: 2px solid var(--ink);
    font-family: "Roboto Condensed", sans-serif; font-weight: 700; font-size: 14px;
    color: var(--ink); padding: 14px 0 0 22px;
  }
  .back-text {
    font-family: "Roboto Condensed", sans-serif; font-size: 15px; line-height: 21px; color: var(--ink-soft);
  }
  .back-text strong { font-weight: 700; color: var(--ink); }
  .ingredients { position: absolute; left: 10px; top: 356px; width: 250px; }
  .maker { position: absolute; left: 10px; top: 420px; width: 250px; }
  .code-area { position: absolute; left: 0; top: 494px; width: 255px; height: 80px; background: var(--white); }
  .site { font-family: "Roboto Condensed", sans-serif; font-size: 15px; padding-top: 15px; }
  .back-left .band { padding-left: 14px; }
  .back-right .band { padding-left: 76px; }

  .back-right .back-text { position: absolute; left: 18px; width: 252px; }
  .back-right .head { font-weight: 700; color: var(--forest); letter-spacing: 0.5px; }
  .use { top: 16px; }
  .warning { top: 92px; }
  .keep {
    top: 318px; padding-top: 8px; border-top: 2px solid var(--rule); border-bottom: 2px solid var(--rule);
    padding-bottom: 8px; color: var(--forest); text-transform: uppercase; font-weight: 300; font-size: 15px;
  }
  .disclaimer {
    top: 430px; background: var(--sage-box); padding: 6px 8px; color: var(--ink);
  }
</style>
</head>
<body>
<div class="canvas">

  <section class="label front">
    <div class="brand">
      <div class="brand-name">Vorna</div>
      <div class="brand-rule"></div>
      <div class="brand-sub">HEALTH SCIENCES</div>
    </div>
    <h1 class="product-name">CALM DRIFT</h1>
    <div class="claim-rule top"></div>
    <p class="claim">RELIEF OF<br>ANXIETY AND STRESS</p>
    <div class="claim-rule bottom"></div>
    <div class="lotus-art" role="img" aria-label="Soft green lotus flower ornament"></div>
    <p class="category">DIETARY SUPPLEMENT</p>
    <div class="band">60 CAPSULES</div>
  </section>

  <section class="label back-left">
    <div class="facts-box">SUPPLEMENT FACTS</div>
    <p class="back-text ingredients"><strong>INGREDIENTS:</strong> Lorem ipsum dolor sit amet, consectetuer adipiscing elit, sed diam</p>
    <p class="back-text maker"><strong>MANUFACTURE:</strong><br>VORNA HEALTH SCIENCES</p>
    <div class="code-area"></div>
    <div class="band site">www.vornahealthsciences.com</div>
  </section>

  <div class="back-divider"></div>

  <section class="label back-right">
    <p class="back-text use"><span class="head">SUGGESTED USE:</span> As a dietary supplement, take one capsule twice daily, preferably with meals.</p>
    <p class="back-text warning"><span class="head">WARNING:</span> If you are pregnant or breastfeeding, do not use this product. If symptoms persist or worsen, or if new symptoms develop, discontinue use and consult a health care practitioner. If you are taking prescription medications, consult a health care practitioner prior to use. Consumption with alcohol, other drugs or natural health products with sedative properties is not recommended.</p>
    <p class="back-text keep">Keep out of reach of children. Do not use if safety seal is damaged or missing. Store in a cool, dry place.</p>
    <p class="back-text disclaimer">These products have not been evaluated by the FDA and are not intended to diagnose, treat, cure, or prevent any disease.</p>
    <div class="band site">www.vornahealthsciences.com</div>
  </section>

</div>
</body>
</html>
```